I need a business card designed using the logo provided either vertical or horizontal......Harbourline Property Group is an Australian based real estate company that caters for the upper end of the market so the design of the business card "must reflect" the companies image!!
Colour combinations are optional but "must be realistic" and must be able to be accurately useable CMYK colours.
Please consider that any colours used "must be able to be used" and be suitable in following designs for "pull out banner signs" and "real estate signs".
The colours and the font in the attached designs are for example and other combinations are encouraged.
Target Market(s)
The High End of the Australian real estate market
Industry/Entity Type
Business
Contact Information for Business Card
Logo - Business Name - Director + Licensed Real Estate Agent - Mobile Number (Cell Phone) - Business Number - Fax - Email Address - Web address
Requirements
Must have
- Designs and colours (CMYK) that can easily be interpreted by an Australian printer.
Nice to have
- Some alternative ideas on colour and font..........the ones provided are ok and have been provided as an example but I am looking for alternative ideas
Should not have
- Loud, overly bright colours. Designs that do not reflect the professional standards of the business.
- Designs that look good on a computer monitor but can not be re-created on a printing press.............this is most important when it comes to shading etc.

```html
<!DOCTYPE html>
<html lang="en">
<head>
<meta charset="utf-8">
<title>Harbourline Property Group – Business Card</title>
<link href="https://fonts.googleapis.com/css2?family=Open+Sans:wght@400;600;700&display=swap" rel="stylesheet">
<style>
  :root {
    --backdrop: #e4e4e4;
    --card-black: #0b0b0c;
    --card-charcoal: #1f2022;
    --gold: #c98a2c;
    --gold-light: #f0cf8a;
    --gold-deep: #8a5a17;
    --text-white: #f4f4f4;
    --text-soft: #d9d9d9;
  }
  * { margin: 0; padding: 0; box-sizing: border-box; }
  html, body {
    width: 1200px; height: 852px; overflow: hidden;
    background: var(--backdrop);
    font-family: "Open Sans", Arial, sans-serif;
  }
  .stage {
    position: relative; width: 1200px; height: 852px;
  }
  .card {
    position: absolute; width: 500px; height: 286px;
    border-radius: 20px; overflow: hidden;
    background: linear-gradient(115deg, var(--card-black) 0%, var(--card-charcoal) 45%, var(--card-black) 100%);
    box-shadow: 0 6px 18px rgba(0,0,0,0.25);
  }
  .card--front { left: 70px; top: 283px; }
  .card--back  { left: 630px; top: 283px; }

  /* brand name block */
  .brand {
    position: absolute; display: flex; align-items: center; gap: 14px;
  }
  .brand__mark {
    width: 34px; height: 34px; background: var(--gold);
  }
  .brand__name {
    color: var(--text-white); font-weight: 600;
    text-transform: uppercase; letter-spacing: 2px; line-height: 1.25;
  }
  .card--front .brand { left: 70px; top: 112px; }
  .card--front .brand__name { font-size: 22px; }

  .card--back .brand { left: 62px; top: 30px; gap: 10px; }
  .card--back .brand__mark { width: 22px; height: 22px; }
  .card--back .brand__name { font-size: 13px; letter-spacing: 1.5px; }

  /* gold edge band on back */
  .gold-band {
    position: absolute; left: 0; top: 0; bottom: 0; width: 36px;
    background: linear-gradient(90deg, var(--gold-deep) 0%, var(--gold-light) 40%, var(--gold) 75%, var(--gold-deep) 100%);
  }
  .gold-rule {
    position: absolute; left: 40px; top: 0; bottom: 0; width: 3px;
    background: var(--gold-light);
  }

  .person {
    position: absolute; right: 28px; top: 34px; text-align: right;
  }
  .person__name { color: var(--gold); font-weight: 700; font-size: 15px; }
  .person__role { color: var(--text-soft); font-size: 11px; margin-top: 2px; }

  .contact {
    position: absolute; left: 62px; bottom: 28px; list-style: none;
    color: var(--text-white); font-size: 12px;
  }
  .contact li { display: flex; align-items: center; gap: 8px; height: 21px; }
  .contact svg { width: 12px; height: 12px; flex: none; }
  .contact .gap { margin-left: 10px; }
</style>
</head>
<body>
<main class="stage">

  <section class="card card--front" aria-label="Card front">
    <div class="brand">
      <span class="brand__mark"></span>
      <span class="brand__name">Harbourline<br>Property Group</span>
    </div>
  </section>

  <section class="card card--back" aria-label="Card back">
    <div class="gold-band"></div>
    <div class="gold-rule"></div>

    <div class="brand">
      <span class="brand__mark"></span>
      <span class="brand__name">Harbourline<br>Property Group</span>
    </div>

    <div class="person">
      <p class="person__name">Your Long Name</p>
      <p class="person__role">Managing Director</p>
    </div>

    <ul class="contact">
      <li>
        <svg viewBox="0 0 12 12" aria-hidden="true"><path fill="#c98a2c" d="M2.5 1l2 2-1 1.2c.6 1.4 1.8 2.6 3.3 3.3L8 6.5l2 2-1.4 2C4.8 10.3 1.7 7.2 1.5 2.4z"/></svg>
        00.00.00.0000
        <svg class="gap" viewBox="0 0 12 12" aria-hidden="true"><rect x="1" y="4" width="10" height="7" rx="1" fill="#c98a2c"/><rect x="3" y="1" width="6" height="4" fill="none" stroke="#c98a2c"/></svg>
        00.00.00.0000
      </li>
      <li>
        <svg viewBox="0 0 12 12" aria-hidden="true"><rect x="1" y="2.5" width="10" height="7" fill="#c98a2c"/><path d="M1 2.5l5 4 5-4" fill="none" stroke="#0b0b0c"/></svg>
        yourname@yourwebsite.com
      </li>
      <li>
        <svg viewBox="0 0 12 12" aria-hidden="true"><circle cx="6" cy="6" r="5" fill="none" stroke="#c98a2c" stroke-width="1.2"/><path d="M1 6h10M6 1c-2.5 3-2.5 7 0 10M6 1c2.5 3 2.5 7 0 10" fill="none" stroke="#c98a2c"/></svg>
        www.yourwebsite.com
      </li>
      <li>
        <svg viewBox="0 0 12 12" aria-hidden="true"><path fill="#c98a2c" d="M6 0.8a3.8 3.8 0 0 1 3.8 3.8C9.8 7.5 6 11.4 6 11.4S2.2 7.5 2.2 4.6A3.8 3.8 0 0 1 6 .8z"/><circle cx="6" cy="4.6" r="1.4" fill="#0b0b0c"/></svg>
        Your Commercial or office address with pin code
      </li>
    </ul>
  </section>

</main>
</body>
</html>
```